Profesional personal website needs design and business card

I need a business card with my professional name as a logo "Dorian Vitality" for my business. I am a Wellness Coach, consultant and trainer. So it should be professional, wellness oriented and modern.

Target Market(s)

Private clients, governments, corporations. Luxury and high market.

Industry/Entity Type

Health And Wellness

Contact Information for Business Card

Dorian Vitality should be the logo

Colors

Designer to choose colors to be used in the design.

Requirements
Must have
• Dorian Vitality
• Name: Tomás Lirandel
• Wellness Coach, Consultant & Trainer.
• Website: www.dorianvitality-example.com
• Phone:
• Spain (+34) 612 480 317
• (USA) +1 (555) 610 4829
Nice to have
• The most important is the design of "Dorian Vitality", as this is going to be my personal brand logo. It should be professional, wellness, high end and actual.
Should not have
• no golds, no baroque style..

```html
<!DOCTYPE html>
<html lang="en">
<head>
<meta charset="UTF-8">
<title>Dorian Vitality — Business Card</title>
<link href="https://fonts.googleapis.com/css2?family=Open+Sans:wght@400;600;700&display=swap" rel="stylesheet">
<style>
  :root {
    --backdrop: #3a3431;
    --card-black: #0d0d0d;
    --card-edge: #1c1c1c;
    --green-deep: #2fa01c;
    --green-bright: #7fd321;
    --text-light: #d6d6d6;
    --divider: #2a2a2a;
    --silver: #d9d9d9;
  }
  * { margin: 0; padding: 0; box-sizing: border-box; }
  html, body {
    width: 1200px;
    height: 844px;
    overflow: hidden;
    background: var(--backdrop);
    font-family: "Open Sans", Arial, sans-serif;
  }
  .canvas {
    position: relative;
    width: 1200px;
    height: 844px;
    display: flex;
    align-items: center;
    justify-content: center;
    gap: 60px;
  }
  .card {
    position: relative;
    width: 510px;
    height: 300px;
    background: var(--card-black);
    border: 1px solid var(--card-edge);
    box-shadow: 0 10px 30px rgba(0,0,0,0.45);
  }

  /* Front */
  .card-front { display: flex; }
  .brand-panel {
    width: 52%;
    display: flex;
    align-items: center;
    justify-content: center;
    gap: 12px;
    padding-top: 30px;
  }
  .brand-dot {
    width: 22px;
    height: 22px;
    border-radius: 50%;
    background: var(--green-deep);
    flex: none;
  }
  .brand-name {
    color: var(--green-deep);
    font-weight: 700;
    font-size: 25px;
    white-space: nowrap;
  }
  .divider {
    width: 1px;
    background: var(--divider);
    margin: 0;
  }
  .contact-panel {
    flex: 1;
    padding: 38px 0 0 20px;
    color: var(--text-light);
  }
  .person-name {
    font-size: 16px;
    font-weight: 700;
    letter-spacing: 0.3px;
    line-height: 1.1;
  }
  .person-name .first { color: var(--green-deep); }
  .person-name .last { color: var(--green-bright); }
  .person-role {
    font-size: 13px;
    line-height: 1.3;
    margin-top: 2px;
  }
  .contact-list {
    list-style: none;
    margin-top: 12px;
    font-size: 12.5px;
    line-height: 1.65;
  }
  .contact-list li { display: flex; align-items: center; gap: 8px; white-space: nowrap; }
  .contact-icon { width: 14px; height: 14px; flex: none; }

  /* Back */
  .card-back {
    display: flex;
    align-items: center;
    justify-content: center;
    gap: 12px;
  }
  .card-back .brand-dot { background: var(--silver); }
  .card-back .brand-name { color: var(--silver); font-size: 24px; }
</style>
</head>
<body>
<main class="canvas">
  <section class="card card-front" aria-label="Business card front">
    <div class="brand-panel">
      <span class="brand-dot"></span>
      <span class="brand-name">Dorian Vitality</span>
    </div>
    <div class="divider"></div>
    <div class="contact-panel">
      <h1 class="person-name"><span class="first">TOMÁS</span> <span class="last">LIRANDEL</span></h1>
      <p class="person-role">Wellness Coach<br>Consultant &amp; Trainer</p>
      <ul class="contact-list">
        <li>
          <svg class="contact-icon" viewBox="0 0 16 16"><circle cx="8" cy="8" r="7" fill="none" stroke="#7fd321" stroke-width="1.4"/><path d="M5.5 4.5l1.3 1.6-.8 1c.6 1.2 1.4 2 2.6 2.6l1-.8 1.6 1.3-.7 1.2C7.8 11.3 4.7 8.2 4.6 5.2z" fill="#7fd321"/></svg>
          (+34) 612 480 317 (SPAIN)
        </li>
        <li>
          <svg class="contact-icon" viewBox="0 0 16 16"><circle cx="8" cy="8" r="7" fill="none" stroke="#7fd321" stroke-width="1.4"/><path d="M5.5 4.5l1.3 1.6-.8 1c.6 1.2 1.4 2 2.6 2.6l1-.8 1.6 1.3-.7 1.2C7.8 11.3 4.7 8.2 4.6 5.2z" fill="#7fd321"/></svg>
          +1 (555) 610 4829 (USA)
        </li>
        <li>
          <svg class="contact-icon" viewBox="0 0 16 16"><circle cx="8" cy="8" r="7.5" fill="#7fd321"/><g fill="none" stroke="#0d0d0d" stroke-width="0.9"><circle cx="8" cy="8" r="5"/><ellipse cx="8" cy="8" rx="2.2" ry="5"/><path d="M3 8h10M4 5.5h8M4 10.5h8"/></g></svg>
          www.dorianvitality-example.com
        </li>
      </ul>
    </div>
  </section>

  <section class="card card-back" aria-label="Business card back">
    <span class="brand-dot"></span>
    <span class="brand-name">Dorian Vitality</span>
  </section>
</main>
</body>
</html>
```